Every Shelf Set Neatly or ESN Organized needs a business card design. ESN Organized is a professi

We need a business card design that is clean, sharp and conveys a sense of organization. I already have a logo.

Target Market(s)

Families (specifically mothers), small business owners, parents, seniors

Industry/Entity Type

Business

Contact Information for Business Card

My website is www.esnorganized-example.com and my sociallink page is http://www.sociallink-example.com/everyshelfsetneatly. The phone number is 418-552-7094 and I want to be listed as Lorna M. Pelham, Owner

Requirements
Must have
• My logo.

```html
<!DOCTYPE html>
<html lang="en">
<head>
<meta charset="utf-8">
<title>ESN Organized – Business Card</title>
<link rel="stylesheet" href="https://fonts.googleapis.com/css2?family=Montserrat:wght@300;400&family=Source+Sans+3:wght@400;600&display=swap">
<style>
  :root {
    --backdrop: #141414;
    --brand-blue: #0a7bd8;
    --card-white: #ffffff;
    --ink: #333333;
    --ink-soft: #444444;
    --on-blue: #ffffff;
  }
  * { margin: 0; padding: 0; box-sizing: border-box; }
  html, body {
    width: 1200px;
    height: 900px;
    overflow: hidden;
    background: var(--backdrop);
  }
  .stage {
    position: relative;
    width: 1200px;
    height: 900px;
  }
  .card {
    position: absolute;
    top: 170px;
    width: 347px;
    height: 561px;
    text-align: center;
  }
  .card--front {
    left: 259px;
    background: var(--card-white);
  }
  .card--back {
    left: 631px;
    background: var(--brand-blue);
    color: var(--on-blue);
  }
  .owner-name {
    position: absolute;
    top: 126px;
    left: 0;
    right: 0;
    font-family: "Source Sans 3", sans-serif;
    font-weight: 600;
    font-size: 23px;
    color: var(--brand-blue);
    letter-spacing: 0.2px;
  }
  .owner-role {
    position: absolute;
    top: 157px;
    left: 0;
    right: 0;
    font-family: "Source Sans 3", sans-serif;
    font-weight: 400;
    font-size: 15px;
    color: var(--ink-soft);
  }
  .brand-name {
    position: absolute;
    left: 0;
    right: 0;
    font-family: "Montserrat", sans-serif;
    font-weight: 300;
    line-height: 1;
  }
  .card--front .brand-name {
    top: 208px;
    font-size: 104px;
    color: var(--brand-blue);
  }
  .card--back .brand-name {
    top: 172px;
    font-size: 86px;
    color: var(--on-blue);
  }
  .contact-list {
    position: absolute;
    top: 358px;
    left: 0;
    right: 0;
    list-style: none;
    font-family: "Source Sans 3", sans-serif;
    font-size: 15.5px;
    line-height: 21px;
    color: var(--ink);
  }
  .tagline-top {
    position: absolute;
    top: 280px;
    left: 0;
    right: 0;
    font-family: "Montserrat", sans-serif;
    font-weight: 400;
    font-size: 20px;
    letter-spacing: 3px;
  }
  .tagline-bottom {
    position: absolute;
    top: 303px;
    left: 0;
    right: 0;
    font-family: "Montserrat", sans-serif;
    font-weight: 400;
    font-size: 31px;
    letter-spacing: 8px;
  }
  .social-handle {
    position: absolute;
    top: 369px;
    left: 0;
    right: 0;
    font-family: "Source Sans 3", sans-serif;
    font-weight: 400;
    font-size: 17px;
  }
</style>
</head>
<body>
  <main class="stage">
    <section class="card card--front" aria-label="Business card front">
      <h1 class="owner-name">LORNA M. PELHAM</h1>
      <p class="owner-role">Owner</p>
      <p class="brand-name">ESN</p>
      <ul class="contact-list">
        <li>418-552-7094</li>
        <li>info@esnorganized-example.com</li>
        <li>www.esnorganized-example.com</li>
      </ul>
    </section>

    <section class="card card--back" aria-label="Business card back">
      <p class="brand-name">ESN</p>
      <p class="tagline-top">Every Shelf Set</p>
      <p class="tagline-bottom">NEATLY</p>
      <p class="social-handle">sociallink/everyshelfsetneatly</p>
    </section>
  </main>
</body>
</html>
```